New Business Card Design Project

We require a business card design for Vexalund, a newly established Indian company.
Our focus is on the development, manufacturing, and export of a diverse array of pharmaceutical products on a global scale. The card should convey a professional appearance, as our primary markets are in Africa, China, and Southeast Asian nations.
We envision a two-sided business card, with the reverse side dedicated to a logo set against a solid color or an elegantly designed pattern. The corners should be rounded. We would appreciate seeing both horizontal and vertical design options. We trust the designer to utilize their expertise in creating this design.

The content for the business card is included in the attached Word file.

Target Market(s)

Our primary markets are in Africa, China, and Southeast Asian, Latin America, Maldives, Sri Lanka

Industry/Entity Type

Pharmaceutical Manufacturing and Export

Contact Information for Business Card

Colors

Designer to choose colors to be used in the design.

Requirements
Must have
• The reverse side of the business card features solely the logo along with the tagline, "Remedies of Life."
Should not have
• The logo should not exceed two instances, encompassing both the front and back sides of the card.

```html
<!DOCTYPE html>
<html lang="en">
<head>
<meta charset="utf-8">
<title>Vexalund Business Card</title>
<link rel="stylesheet" href="https://fonts.googleapis.com/css2?family=Lato:wght@400;700&family=Montserrat:wght@700&display=swap">
<style>
  :root {
    --backdrop: #4e545c;
    --brand-blue: #18b1f3;
    --brand-blue-soft: #3cbdf5;
    --ink-blue: #27a4df;
    --accent-red: #ef5f4c;
    --ink: #1f1f1f;
    --paper: #ffffff;
  }
  * { margin: 0; padding: 0; box-sizing: border-box; }
  html, body { width: 1200px; height: 1120px; overflow: hidden; }
  body { background: var(--backdrop); position: relative; font-family: "Lato", sans-serif; }

  .card { position: absolute; border-radius: 27px; overflow: hidden; box-shadow: 8px 10px 18px rgba(0,0,0,.28); }

  .card-back { left: 156px; top: 120px; width: 726px; height: 414px; background: var(--brand-blue); }
  .back-pattern { position: absolute; inset: 0;
    background: radial-gradient(ellipse at center, var(--brand-blue) 30%, var(--brand-blue-soft) 100%); opacity: .7; }
  .back-name { position: absolute; left: 0; right: 0; top: 242px; text-align: center;
    font-family: "Montserrat", sans-serif; font-weight: 700; font-size: 54px; color: var(--paper); line-height: 1; }
  .back-tagline { position: absolute; left: 0; right: 0; top: 344px; text-align: center;
    font-family: "Montserrat", sans-serif; font-weight: 700; font-size: 29px; color: var(--paper); line-height: 1; }

  .card-front { left: 322px; top: 607px; width: 702px; height: 400px; background: var(--paper); }
  .front-name { position: absolute; left: 60px; width: 294px; top: 230px; text-align: center;
    font-family: "Montserrat", sans-serif; font-weight: 700; font-size: 44px; color: var(--ink-blue); line-height: 1; }
  .divider { position: absolute; left: 346px; top: 88px; width: 2px; height: 222px; background: var(--ink-blue); }

  .person { position: absolute; left: 383px; top: 92px; }
  .person-name { font-size: 29px; font-weight: 400; color: var(--ink-blue); line-height: 1; letter-spacing: -.3px; }
  .person-title { margin-top: 10px; font-size: 19px; color: var(--ink); line-height: 1; }

  .contact { position: absolute; left: 378px; font-size: 16.5px; color: var(--ink); line-height: 22px; }
  .contact-list { top: 180px; }
  .contact-address { top: 262px; }
  .contact-row { display: flex; align-items: flex-start; }
  .contact-row svg { width: 16px; height: 16px; margin-top: 3px; margin-right: 12px; flex: none; fill: var(--accent-red); }
</style>
</head>
<body>
  <section class="card card-back">
    <div class="back-pattern" role="img" aria-label="Repeating faint pattern in lighter blue across the card"></div>
    <div class="back-name">Vexalund</div>
    <div class="back-tagline">Remedies of Life</div>
  </section>

  <section class="card card-front">
    <div class="front-name">Vexalund</div>
    <div class="divider"></div>

    <div class="person">
      <div class="person-name">DANIEL HARROW</div>
      <div class="person-title">MANAGING DIRECTOR</div>
    </div>

    <div class="contact contact-list">
      <div class="contact-row">
        <svg viewBox="0 0 16 16"><path d="M3.5 1.5l2.5 0 1 3.5-1.6 1.2a8 8 0 0 0 4.4 4.4L11 9l3.5 1v2.5c0 .8-.7 1.5-1.5 1.5C7 14 2 9 2 3c0-.8.7-1.5 1.5-1.5z"/></svg>
        <span>044-987 650 312</span>
      </div>
      <div class="contact-row">
        <svg viewBox="0 0 16 16"><path d="M1 3.5h14v9H1z M1.5 4l6.5 5 6.5-5" stroke="#fff" stroke-width="1.2"/></svg>
        <span>info@vexalund.com</span>
      </div>
      <div class="contact-row">
        <svg viewBox="0 0 16 16"><circle cx="8" cy="8" r="7"/><path d="M3 6c2 0 3 1 2.5 3S7 12 7 14M9 2c0 2 1 3 3 3s2 2 1 4" stroke="#fff" stroke-width="1.2" fill="none"/></svg>
        <span>www.vexalund.com</span>
      </div>
    </div>

    <div class="contact contact-address">
      <div class="contact-row">
        <svg viewBox="0 0 16 16"><path d="M8 1a5 5 0 0 1 5 5c0 4-5 9-5 9S3 10 3 6a5 5 0 0 1 5-5z"/><circle cx="8" cy="6" r="1.8" fill="#fff"/></svg>
        <span>421, Address line goes here<br>45452, Country name</span>
      </div>
    </div>
  </section>
</body>
</html>
```